Podcast Cover Art for rebranded podcast - I have inspiration for the designs

I've had a podcast ("Paperboat Radio Hour") since 2018, but I'm in the process of rebranding it. I've attached the old cover art below, which I loved, but I don't need it to look like that at all. The rebranded podcast is called 'Open Window with Marnie Cole.' I've included the show description at the bottom. I've been working on various design options in Canva, but not obsessed with anything yet, but I'm attaching the ones I do like that I think just need some refining. My very favorite is the one labeled 'favorite_Open Window' so I wouldn't mind keeping that general idea but perfected by a designer. Ultimately, I want something cool, fairly clean, modern, eye catching. I'm into neutrals with maybe a pop of color, so think black, white, grey..maybe silver, and I love a pop of red..and I'm not opposed to other options for the pop color. The show is going to be inspiring, entertaining, and funny. Oh and one other idea I had but I'm not sure if it makes sense with the title and/or what the show is about..but a vinyl record with Open Window with Marnie Cole on it somehow, on a record player..not sure.

Ever wonder what it means to truly live authentically? Curious about how to embrace the unpredictability of life? Ready for some heartfelt and lighthearted conversations that inspire and entertain?
Join Marnie Cole as she dives into the raw, real, and unscripted moments of life. In each episode, Marnie brings candid conversations and genuine insights into the ups and downs we all experience. From personal growth and self-discovery to inspiring stories and valuable life lessons, "Open Window" is a space where authenticity reigns and spontaneity is celebrated.
Whether she's sharing her own journey or chatting with inspiring guests, Marnie invites you to explore the beauty of living life without a script. Expect honest reflections, thought-provoking discussions, and a refreshing perspective on navigating life's unpredictable path—all with a dash of fun and humor to keep things lively and entertaining. Step into the unscripted moments of life and tune in for a blend of depth and lightheartedness that will leave you inspired, smiling, and most importantly laughing.

Target Market(s)

25-50 year old women and men (primarily women)

Font styles to use
Sans Serif

Requirements
Should not have
• nothing too feminine or girly, nothing cheesy :)

```html
<!DOCTYPE html>
<html lang="en">
<head>
<meta charset="UTF-8">
<title>Open Window with Marnie Cole — Podcast Cover</title>
<link href="https://fonts.googleapis.com/css2?family=Anton&family=Montserrat:wght@800&family=Oswald:wght@600&display=swap" rel="stylesheet">
<style>
  :root {
    --paper: #f3f3f3;
    --ink: #3a3a3a;
    --red: #e0140f;
    --photo-warm: #b0713f;
    --photo-deep: #3b2418;
  }
  * { margin: 0; padding: 0; box-sizing: border-box; }
  html, body {
    width: 1200px;
    height: 1200px;
    overflow: hidden;
    background: var(--paper);
  }
  .cover {
    position: relative;
    width: 1200px;
    height: 1200px;
    background: linear-gradient(160deg, #f7f7f7 0%, var(--paper) 55%, #ececec 100%);
    overflow: hidden;
  }
  .cover__frame {
    position: absolute;
    left: 0; top: 0;
    width: 1200px; height: 1200px;
  }
  .cover__accent-circle {
    position: absolute;
    left: 660px;
    top: 238px;
    width: 724px;
    height: 724px;
    border-radius: 50%;
    background: var(--red);
  }
  .cover__host-photo {
    position: absolute;
    left: 745px;
    top: 135px;
    width: 455px;
    height: 1065px;
    border-radius: 200px 120px 0 40px;
    background: linear-gradient(180deg, var(--photo-deep) 0%, var(--photo-warm) 30%, #d9c6b4 62%, var(--photo-deep) 100%);
  }
  .title {
    position: absolute;
    left: 118px;
    display: block;
    font-family: "Anton", "Oswald", sans-serif;
    line-height: 1;
    text-transform: uppercase;
    white-space: nowrap;
  }
  .title__main {
    top: 140px;
    font-size: 270px;
    color: var(--ink);
    letter-spacing: 0;
    transform: scale(1, 1.3);
    transform-origin: left top;
  }
  .title__accent {
    top: 488px;
    font-size: 122px;
    color: var(--red);
    letter-spacing: 0;
    transform: scale(1.3, 1);
    transform-origin: left top;
  }
  .byline__with {
    position: absolute;
    left: 267px;
    top: 788px;
    width: 269px;
    height: 96px;
    border: 3px solid var(--red);
    border-radius: 48px;
    display: flex;
    align-items: center;
    justify-content: center;
    font-family: "Montserrat", sans-serif;
    font-weight: 800;
    font-size: 58px;
    letter-spacing: 6px;
    color: var(--ink);
  }
  .byline__host {
    position: absolute;
    left: 101px;
    top: 900px;
    font-family: "Oswald", sans-serif;
    font-weight: 600;
    font-size: 128px;
    line-height: 1.1;
    color: var(--ink);
    white-space: nowrap;
  }
</style>
</head>
<body>
  <main class="cover">
    <svg class="cover__frame" viewBox="0 0 1200 1200" aria-hidden="true">
      <rect x="44" y="69" width="1113" height="1062" rx="66" fill="none" stroke="#e0140f" stroke-width="3"/>
    </svg>
    <div class="cover__accent-circle"></div>
    <div class="cover__host-photo" role="img" aria-label="Photo of host Marnie Cole seated, smiling, long dark hair, white top, sunglasses on head"></div>
    <h1>
      <span class="title title__main">Open</span>
      <span class="title title__accent">Window</span>
    </h1>
    <div class="byline__with">WITH</div>
    <p class="byline__host">Marnie Cole</p>
  </main>
</body>
</html>
```